Homepage layout for online ad network

Attached is our Valtro Media logo and updated brief (I can't seem to delete the old logo and brief, but they're no longer relevant).

This project was originally posted with a different logo and corporate name, but we have decided to stay with our current logo and name and redesign the site.

Your design is for a homepage only - design, no coding (I'll get someone else to take your PSD and code it).

Your homepage will make use of a Flash slider - BUT YOU ARE NOT REQUIRED TO PROVIDE THE FLASH. Instead, simply provide the layout and at least two static examples out of the four different sections that will eventually be in the slider.

Much of this design is based on the design of a competitor (listed in the brief).

Please ask whatever questions you need to in order to clarify instructions.
Updates

Project updated to include new logo (and correspondingly new color scheme).

Brief changed slightly.

Thank you for submitting designs for this project in the past.

After some internal strategy work, we have decided to retain our initial corporate identity, Valtro Media.

If you have submitted a design for the original brief and are available, please re-work your best prior design to reflect the color scheme in the newly uploaded logo.

Target Market(s)

This site is aimed primarily at young professionals who buy digital media on behalf of large advertisers.

Industry/Entity Type

Media

Requirements
Must have
• modern white space
Should not have
• no Flash outside of slider

```html
<!DOCTYPE html>
<html lang="en">
<head>
<meta charset="utf-8">
<title>Valtro Media — Homepage</title>
<link rel="stylesheet" href="https://fonts.googleapis.com/css2?family=Montserrat:wght@400;600;700&family=Arimo:wght@400;700&family=Roboto+Condensed:wght@300;400;700&display=swap">
<style>
  :root {
    --red: #c4162f;
    --red-bright: #d80e27;
    --red-deep: #87151f;
    --ink: #1d1d1f;
    --text: #333333;
    --panel: #f8f8f8;
    --lime: #d4e22c;
    --lime-light: #eef571;
    --white: #ffffff;
    --slide-light: #f4f5f7;
    --slide-mid: #dfe2e6;
  }
  * { box-sizing: border-box; margin: 0; padding: 0; }
  html, body { width: 1200px; height: 1000px; overflow: hidden; background: var(--white); }
  body { position: relative; font-family: "Arimo", Arial, sans-serif; color: var(--text); }

  /* Header */
  .site-header { position: absolute; top: 0; left: 0; width: 1200px; height: 116px; background: var(--white); }
  .brand { position: absolute; left: 136px; top: 28px; display: flex; align-items: center; gap: 12px; }
  .brand-mark { width: 22px; height: 22px; background: var(--red); }
  .brand-name { font-family: "Montserrat", sans-serif; font-weight: 600; font-size: 34px; color: var(--ink); letter-spacing: -0.5px; }
  .brand-pointer { position: absolute; left: 254px; top: 102px; width: 0; height: 0; border-left: 7px solid transparent; border-right: 7px solid transparent; border-bottom: 12px solid var(--red); }
  .tagline { position: absolute; right: 119px; top: 26px; font-family: "Montserrat", sans-serif; font-weight: 600; font-size: 11.5px; color: var(--red); letter-spacing: 0.3px; }
  .main-nav { position: absolute; right: 118px; top: 68px; display: flex; height: 33px; }
  .main-nav a { display: flex; align-items: center; padding: 0 14px; font-family: "Montserrat", sans-serif; font-weight: 700; font-size: 12.5px; color: var(--ink); text-decoration: none; letter-spacing: 0.3px; border-left: 1px solid #555; }
  .main-nav a:first-child { border-left: 0; }
  .main-nav a:nth-child(2) { border-left-color: var(--red); }
  .main-nav a:last-child { padding-right: 0; }
  .header-rule { position: absolute; left: 0; top: 116px; width: 1200px; height: 4px; border-top: 2px solid var(--red); background: var(--white); }

  /* Hero band */
  .hero { position: absolute; top: 120px; left: 0; width: 1200px; height: 425px; background: linear-gradient(180deg, var(--red-bright) 0%, #b8122a 50%, var(--red-deep) 100%); }
  .slide { position: absolute; left: 123px; top: 30px; width: 960px; height: 350px; background: linear-gradient(90deg, var(--slide-mid) 0%, var(--white) 25%, var(--slide-light) 60%, #e8ecf2 100%); box-shadow: 0 6px 10px rgba(0,0,0,0.45); overflow: hidden; }
  .slide-photo { position: absolute; left: 505px; top: 0; width: 365px; height: 350px; background: radial-gradient(ellipse at 55% 45%, #d9ab8e 0%, #a0705a 35%, #4a2d22 65%, rgba(232,236,242,0) 85%); }
  .slide-title { position: absolute; left: 104px; top: 120px; font-family: "Montserrat", sans-serif; font-weight: 700; font-size: 39px; color: var(--red); letter-spacing: 0.5px; line-height: 1; }
  .slide-sub { position: absolute; left: 105px; top: 165px; font-family: "Montserrat", sans-serif; font-weight: 400; font-size: 20px; line-height: 24px; color: var(--ink); letter-spacing: 0.4px; }
  .slide-arrow { position: absolute; top: 155px; width: 30px; height: 52px; }
  .slide-arrow.prev { left: 20px; }
  .slide-arrow.next { right: 16px; }
  .slider-dots { position: absolute; left: 526px; top: 396px; display: flex; gap: 13px; }
  .slider-dots span { width: 15px; height: 15px; border-radius: 50%; background: #1a1a1a; }
  .slider-dots span.active { background: var(--white); }

  /* Content */
  .content-panel { position: absolute; left: 118px; top: 658px; width: 960px; height: 247px; background: var(--panel); box-shadow: 0 10px 12px -6px rgba(0,0,0,0.3); }
  .news-panel { position: absolute; left: 729px; top: 598px; width: 349px; height: 307px; background: linear-gradient(180deg, var(--white) 0%, var(--panel) 20%); box-shadow: -8px 0 10px -8px rgba(0,0,0,0.25); }

  .about-heading { position: absolute; left: 124px; top: 567px; display: flex; align-items: center; gap: 12px; font-family: "Roboto Condensed", sans-serif; font-size: 25px; color: var(--ink); letter-spacing: 0.3px; }
  .about-heading .mark { width: 16px; height: 16px; background: var(--red); }
  .about-heading strong { font-weight: 700; }
  .about-lead { position: absolute; left: 123px; top: 608px; width: 560px; font-size: 18px; line-height: 24px; color: var(--red); }
  .about-body { position: absolute; left: 122px; top: 666px; width: 540px; font-size: 14px; line-height: 24.2px; color: var(--text); }
  .about-rule { position: absolute; left: 122px; top: 835px; width: 577px; height: 1px; background: #555; }
  .about-links { position: absolute; left: 120px; top: 853px; display: flex; font-family: "Montserrat", sans-serif; font-weight: 600; font-size: 13px; color: var(--ink); letter-spacing: 0.3px; }
  .about-links a { color: inherit; text-decoration: none; display: flex; align-items: center; gap: 5px; }
  .about-links svg { width: 13px; height: 11px; }

  .news-label { position: absolute; left: 729px; top: 558px; width: 240px; height: 39px; background: linear-gradient(90deg, var(--lime-light) 0%, var(--lime) 40%, var(--lime) 90%, var(--lime-light) 100%); box-shadow: 0 2px 4px rgba(0,0,0,0.35); font-family: "Roboto Condensed", sans-serif; font-size: 25px; color: var(--red); padding: 4px 0 0 31px; letter-spacing: 0.3px; }
  .news-list { position: absolute; left: 767px; top: 615px; width: 300px; list-style: none; }
  .news-list li { height: 64px; }
  .news-date { display: block; font-weight: 700; font-size: 12px; color: var(--red); letter-spacing: 0.4px; line-height: 14px; }
  .news-text { display: block; font-size: 12px; line-height: 16px; color: var(--ink); margin-top: 2px; }

  .copyright { position: absolute; left: 0; top: 924px; width: 1246px; text-align: center; font-size: 12px; color: var(--ink); }
</style>
</head>
<body>
  <header class="site-header">
    <div class="brand">
      <span class="brand-mark"></span>
      <span class="brand-name">Valtro Media</span>
    </div>
    <span class="brand-pointer"></span>
    <p class="tagline">COMPANY TAGLINE GOES HERE</p>
    <nav class="main-nav">
      <a href="#">BEAUTY</a>
      <a href="#">COOKING</a>
      <a href="#">PARENTING</a>
      <a href="#">ENTERTAINMENT</a>
      <a href="#">VIDEO</a>
      <a href="#">CPC</a>
    </nav>
  </header>
  <div class="header-rule"></div>

  <section class="hero">
    <div class="slide">
      <div class="slide-photo" role="img" aria-label="Photo of a woman with yellow flowers in her hair"></div>
      <h1 class="slide-title">BEAUTY</h1>
      <p class="slide-sub">SITE SPECIFIC CAMPAIGNS<br>AT RON PRICES</p>
      <svg class="slide-arrow prev" viewBox="0 0 30 52" aria-label="Previous slide"><path d="M24 2 L6 26 L24 50 L16 50 L0 26 L16 2 Z" fill="#1a1a1a"/></svg>
      <svg class="slide-arrow next" viewBox="0 0 30 52" aria-label="Next slide"><path d="M6 2 L24 26 L6 50 L14 50 L30 26 L14 2 Z" fill="#1a1a1a"/></svg>
    </div>
    <div class="slider-dots"><span class="active"></span><span></span><span></span><span></span><span></span><span></span></div>
  </section>

  <div class="content-panel"></div>
  <div class="news-panel"></div>

  <section class="about">
    <h2 class="about-heading"><span class="mark"></span><span>ABOUT <strong>VALTRO MEDIA</strong></span></h2>
    <p class="about-lead">Lorem ipsum dolor sit amet, consectetur adipiscing elit. Mauris dignissim nulla pharetra risus iaculis at consequat turpis vulputate.</p>
    <p class="about-body">Sed scelerisque magna ut quam scelerisque dictum. Morbi purus quam, sodales id vehicula non, ultricies vitae justo. Vivamus sed augue ut elit dapibus adipiscing vel in elit. Mauris adipiscing, elit a laoreet eleifend, orci lacus condimentum enim, vitae venenatis enim velit ac dolor. Nullam augue mauris, tincidunt et bibendum nec, consequat ut dui. Sed id ante in purus vulputate adipiscing ac non justo. Nulla libero sem, venenatis in fringilla pulvinar, ornare ac diam.</p>
    <div class="about-rule"></div>
    <nav class="about-links">
      <a href="#" style="width:110px">ABOUT US <svg viewBox="0 0 13 11"><path d="M0 5.5 H10 M6 1 L11 5.5 L6 10" stroke="#c4162f" stroke-width="2" fill="none"/></svg></a>
      <a href="#" style="width:133px">CONTACT US <svg viewBox="0 0 13 11"><path d="M0 5.5 H10 M6 1 L11 5.5 L6 10" stroke="#c4162f" stroke-width="2" fill="none"/></svg></a>
      <a href="#" style="width:180px">MANAGEMENT TEAM <svg viewBox="0 0 13 11"><path d="M0 5.5 H10 M6 1 L11 5.5 L6 10" stroke="#c4162f" stroke-width="2" fill="none"/></svg></a>
      <a href="#" style="width:82px">NEWS <svg viewBox="0 0 13 11"><path d="M0 5.5 H10 M6 1 L11 5.5 L6 10" stroke="#c4162f" stroke-width="2" fill="none"/></svg></a>
      <a href="#">CAREERS <svg viewBox="0 0 13 11"><path d="M0 5.5 H10 M6 1 L11 5.5 L6 10" stroke="#c4162f" stroke-width="2" fill="none"/></svg></a>
    </nav>
  </section>

  <aside class="news">
    <h2 class="news-label">VALTRO NEWS</h2>
    <ul class="news-list">
      <li><span class="news-date">JANUARY 15, 2011</span><span class="news-text">Valtro Media unveils new web site design and digital strategy</span></li>
      <li><span class="news-date">DECEMBER 22, 2010</span><span class="news-text">Valtro Media featured in Foundermag.com as one of the fastest grown online ad agencies.</span></li>
      <li><span class="news-date">NOVEMBER 15, 2010</span><span class="news-text">As RTB Goes Mainstream, Display Services Try To Pull Publishers Along</span></li>
      <li><span class="news-date">NOVEMBER 9, 2010</span><span class="news-text">Morbi purus quam, sodales id vehicula non, ultricies vitae justo</span></li>
    </ul>
  </aside>

  <footer class="copyright">Copyright 2011 Valtro Media. All Rights Reserved</footer>
</body>
</html>
```